Building Referrer Relationships Booklet

4 page A4 booklet to give to potential professional referrers to establish a collaborative relationship.Needs to be bright, vibrant, colourful, friendly, inviting, in keeping with The Linden Practice colours.
Want to provide potential referrer partners a great reason to choose to collaborate with us. They need to know who we are, what makes us different/appealing, and who we are looking for to connect with.
The final product should communicate high performance and connectedness.
Updates

Target Market(s)

professional medical allied health and fitness practitioners

Industry/Entity Type

Health

Requirements
Must have
• energetic, vibrant, engaging, inviting, images

```html
<!DOCTYPE html>
<html lang="en">
<head>
<meta charset="utf-8">
<title>Referral Partners Required – The Linden Practice</title>
<link href="https://fonts.googleapis.com/css2?family=Raleway:wght@400;500;700;800&display=swap" rel="stylesheet">
<style>
  :root {
    --backdrop: #e9e9ea;
    --paper: #ffffff;
    --navy: #223b96;
    --blue: #0b6cc6;
    --orange: #f26a1b;
    --amber: #f8a31d;
    --white: #ffffff;
    --ink: #4a4a4a;
    --ink-dark: #2b2b2b;
    --rule: #c9c9c9;
    --grey-band: #d4d6d9;
  }
  * { margin: 0; padding: 0; box-sizing: border-box; }
  html, body { width: 888px; height: 1200px; overflow: hidden; }
  body { background: var(--backdrop); font-family: "Raleway", sans-serif; position: relative; }

  .flyer { position: absolute; left: 86px; top: 80px; width: 716px; height: 1012px; background: var(--paper); overflow: hidden; }
  .flyer-shapes { position: absolute; inset: 0; }

  .photo-circle { position: absolute; border-radius: 50%; border: 7px solid var(--orange); box-shadow: 0 0 0 6px var(--white); }
  .photo-circle--spa { left: 443px; top: 271px; width: 228px; height: 228px;
    background: radial-gradient(circle at 45% 50%, #f1d8c6 0%, #e7c3aa 35%, #f4f1ee 70%, #dfe4ea 100%); }
  .photo-circle--foot { left: 85px; top: 669px; width: 134px; height: 134px; border-width: 5px; box-shadow: 0 0 0 5px var(--white);
    background: radial-gradient(circle at 50% 50%, #efd2bf 0%, #e6c1a8 40%, #f2f2f2 80%); }

  .partners { position: absolute; left: 0; top: 0; color: var(--white); }
  .partners-title { position: absolute; left: 42px; top: 438px; width: 400px; font-weight: 800; font-size: 20.5px; letter-spacing: .2px; color: var(--orange); }
  .partner { position: absolute; width: 205px; }
  .partner h3 { font-weight: 700; font-size: 14.5px; line-height: 16px; color: var(--amber); position: relative; padding-left: 9px; }
  .partner h3::before { content: ""; position: absolute; left: 0; top: 5px; width: 4px; height: 4px; background: var(--amber); }
  .partner p { font-size: 12px; line-height: 16px; padding-left: 9px; font-weight: 500; }

  .footer-brand { position: absolute; left: 40px; top: 827px; width: 150px; text-align: center; }
  .brand-mark { width: 122px; height: 122px; margin: 0 auto; border-radius: 50%; background: var(--blue); border: 4px solid var(--orange); }
  .brand-name { margin-top: 8px; font-weight: 700; font-size: 17px; color: var(--navy); white-space: nowrap; }

  .contact { position: absolute; left: 241px; top: 867px; color: var(--ink); font-size: 12.5px; line-height: 16px; }
  .contact-name { font-weight: 700; font-size: 14.5px; color: var(--navy); margin-bottom: 1px; }
  .contact-row { display: flex; gap: 5px; }
  .contact-row svg { flex: none; margin-top: 2px; }
  .contact-lines { font-weight: 500; }
  .contact-links { margin-top: 20px; font-weight: 700; color: var(--navy); }
  .contact-links .contact-row { align-items: center; }
  .contact-links .web { font-size: 13.5px; }

  .divider { position: absolute; left: 440px; top: 864px; width: 1px; height: 124px; background: var(--rule); }

  .badges { position: absolute; left: 466px; top: 880px; width: 210px; }
  .badge-label { position: absolute; font-weight: 700; font-size: 11px; color: var(--ink-dark); }
  .badge { position: absolute; height: 20px; border-radius: 2px; }
</style>
</head>
<body>
  <main class="flyer">
    <svg class="flyer-shapes" width="716" height="1012" viewBox="0 0 716 1012" aria-hidden="false">
      <defs>
        <linearGradient id="photoTone" x1="0" y1="0" x2="1" y2="1">
          <stop offset="0" stop-color="#e9e9ea"/>
          <stop offset=".35" stop-color="#d8b39a"/>
          <stop offset=".6" stop-color="#c58f73"/>
          <stop offset="1" stop-color="#3d3d42"/>
        </linearGradient>
        <linearGradient id="panelBlue" x1="0" y1="0" x2="1" y2="0">
          <stop offset="0" stop-color="#233a94"/>
          <stop offset="1" stop-color="#0b6cc6"/>
        </linearGradient>
        <linearGradient id="swoosh" x1="0" y1="0" x2="1" y2="0">
          <stop offset="0" stop-color="#e9461c"/>
          <stop offset="1" stop-color="#f7941d"/>
        </linearGradient>
      </defs>
      <rect class="hero-photo" x="0" y="0" width="716" height="400" fill="url(#photoTone)" role="img" aria-label="Photo of a therapist massaging a woman's shoulder"/>
      <path d="M0,358 C230,370 480,330 716,244 L716,1012 L0,1012 Z" fill="var(--grey-band)"/>
      <path d="M0,372 C230,382 480,342 716,256 L716,1012 L0,1012 Z" fill="var(--white)"/>
      <path d="M0,398 C240,405 480,360 716,270 L716,770 C520,795 300,805 0,658 Z" fill="url(#panelBlue)"/>
      <path d="M0,658 C300,805 520,795 716,770 L716,812 C520,832 260,820 0,690 Z" fill="url(#swoosh)"/>
      <path d="M0,684 C260,814 520,826 716,806 L716,1012 L0,1012 Z" fill="var(--white)"/>
    </svg>

    <div class="photo-circle photo-circle--spa" role="img" aria-label="Photo of a relaxed woman receiving a back massage"></div>
    <div class="photo-circle photo-circle--foot" role="img" aria-label="Photo of hands treating a foot"></div>

    <section class="partners">
      <h2 class="partners-title">REFERRAL PARTNERS REQUIRED:</h2>

      <div class="partner" style="left:42px;top:471px">
        <h3>Massage therapists</h3>
        <p>Deep tissue and remedial massage<br>Therapeutic massage</p>
      </div>
      <div class="partner" style="left:42px;top:533px">
        <h3>Fascial therapists</h3>
        <p>Kinetic chain fascial releases to reset the alignment of the whole body</p>
      </div>
      <div class="partner" style="left:42px;top:612px">
        <h3>Physiotherapists</h3>
        <p>Pain relief, protect and strengthen both lower limb and upper limb</p>
      </div>

      <div class="partner" style="left:255px;top:471px">
        <h3>GP, Sports Physicians</h3>
        <p>General health, diagnostics, treatment support, prescription medications<br>Specialist referrals</p>
      </div>
      <div class="partner" style="left:255px;top:565px">
        <h3>Osteopaths and chiropractors</h3>
        <p>Mobilisation and manipulative therapy for the spinal column and limbs</p>
      </div>
      <div class="partner" style="left:255px;top:659px">
        <h3>Dietician and nutritionists</h3>
        <p>DEXA scan for bone density/lean mass/fat mass<br>Optimising gut health and nutrition - You are what you eat!</p>
      </div>

      <div class="partner" style="left:469px;top:534px">
        <h3>Psychologists/psychiatrists</h3>
        <p>Sometimes our physical body cannot get better until we optimise a healthy mind</p>
      </div>
      <div class="partner" style="left:469px;top:612px">
        <h3>Personal trainers, Pilates and yoga instructors</h3>
        <p>Create awesome body strength, flexibility and resilience</p>
      </div>
      <div class="partner" style="left:469px;top:690px">
        <h3>Surgeons</h3>
        <p>When conservative methods are ineffective, surgical intervention works well.</p>
      </div>
    </section>

    <div class="footer-brand">
      <div class="brand-mark"></div>
      <div class="brand-name">The Linden Practice</div>
    </div>

    <address class="contact" style="font-style:normal">
      <div class="contact-name">The Linden Practice</div>
      <div class="contact-row">
        <svg width="9" height="12" viewBox="0 0 9 12"><path d="M4.5,0 A4.5,4.5 0 0 1 9,4.5 C9,7.5 4.5,12 4.5,12 C4.5,12 0,7.5 0,4.5 A4.5,4.5 0 0 1 4.5,0 Z" fill="var(--orange)"/><circle cx="4.5" cy="4.5" r="1.7" fill="var(--white)"/></svg>
        <div class="contact-lines">Harbourview Centre<br>12 / 215 Marlow Rd<br>Westhaven WA 6099 (Perth)</div>
      </div>
      <div class="contact-links">
        <div class="contact-row">
          <svg width="12" height="11" viewBox="0 0 12 11"><path d="M1,3 C1,1 3,0.5 6,0.5 C9,0.5 11,1 11,3 L9,4 L8,2.5 L4,2.5 L3,4 Z M3,5 L9,5 L10,10 L2,10 Z" fill="var(--orange)"/><circle cx="6" cy="7.3" r="1.4" fill="var(--white)"/></svg>
          <span>(08) 9100 2468</span>
        </div>
        <div class="contact-row">
          <svg width="12" height="12" viewBox="0 0 12 12"><circle cx="6" cy="6" r="5.2" fill="none" stroke="var(--orange)" stroke-width="1.4"/><ellipse cx="6" cy="6" rx="2.2" ry="5.2" fill="none" stroke="var(--orange)" stroke-width="1.2"/><line x1="1" y1="6" x2="11" y2="6" stroke="var(--orange)" stroke-width="1.2"/></svg>
          <span class="web">www.lindenpractice.net</span>
        </div>
      </div>
    </address>

    <div class="divider"></div>

    <div class="badges">
      <span class="badge-label" style="left:6px;top:0">TLP LOGO</span>
      <span class="badge-label" style="left:110px;top:0">SRA LOGO</span>
      <div class="badge" style="left:0;top:32px;width:84px;background:var(--blue)"></div>
      <div class="badge" style="left:110px;top:32px;width:80px;background:#b9b9bb"></div>
      <div class="badge" style="left:0;top:70px;width:86px;height:24px;background:#c8282d"></div>
      <span class="badge-label" style="left:114px;top:78px">NEST LOGO</span>
    </div>
  </main>
</body>
</html>
```